Wordpress Design Project

We need a wordpress design for a new creative innovation company based in Melbourne called BrightForge.
We develop innovative growth and communication strategies for our clients who are generally medium sized businesses wanting to find new ways to grow their businesses.
Our Services include:
Business Strategy
Communications and Strategic Planning
Creative Consultancy
Professional Development
Change Management
Project Management
We would like our wordpress design to be simple and professional yet give a feeling of innovation, kind of like old meeting new.
We are leaning towards the predominant background colour being white, but open to suggestions.
Attached are logo files.
If you require any further information please contact us via the Mosaic Bazaar site.
Communication

```html
<!DOCTYPE html>
<html lang="en">
<head>
<meta charset="utf-8">
<title>BrightForge</title>
<link href="https://fonts.googleapis.com/css2?family=Source+Sans+3:wght@300;400;600&display=swap" rel="stylesheet">
<style>
:root{
  --green:#8cc63f;
  --green-light:#b5dd5a;
  --green-dark:#6a9e26;
  --text:#4a4a4a;
  --muted:#666;
  --gray-tab:#7a7a7a;
  --gray-tab-dark:#555;
  --line:#d6d6d6;
  --panel:#e9e9e9;
}
*{box-sizing:border-box;margin:0;padding:0}
html,body{width:1200px;height:1134px;overflow:hidden;background:#fff}
body{position:relative;font-family:"Source Sans 3",sans-serif;color:var(--text)}
.abs{position:absolute}
.logo{left:160px;top:12px;font-size:37px;font-weight:400;color:var(--green);letter-spacing:-.5px;display:flex;align-items:center;gap:8px}
.logo .mark{width:14px;height:14px;border-radius:50%;background:var(--green)}
.nav{left:524px;top:20px;display:flex;gap:3px}
.nav a{display:block;width:83px;height:30px;line-height:30px;text-align:center;font-size:12.5px;color:#fff;text-decoration:none;background:linear-gradient(#8a8a8a,#606060);position:relative}
.nav a.active{background:linear-gradient(var(--green-light),var(--green));color:#222}
.nav a.active::after{content:"";position:absolute;left:50%;bottom:-6px;margin-left:-6px;border:6px solid transparent;border-bottom:0;border-top-color:var(--green)}
.hero{left:161px;top:69px;width:876px;height:356px;background:linear-gradient(180deg,#d9dcde,#b9bec2 55%,#e8e9ea);box-shadow:0 14px 14px -10px rgba(0,0,0,.35)}
.dots{left:547px;top:398px;width:108px;height:28px;background:#fff;border-radius:8px 8px 0 0;display:flex;justify-content:center;align-items:center;gap:5px}
.dots span{width:9px;height:9px;border-radius:50%;background:#333}
.dots span.on{background:var(--green)}
.welcome h1{font-size:22px;font-weight:300;color:#333}
.welcome{left:163px;top:454px;width:355px}
.welcome p{margin-top:8px;font-size:12px;line-height:21.2px;text-align:justify}
.thumb{left:539px;top:455px;width:204px;height:137px;background:linear-gradient(135deg,#cfd7dc,#8e9aa2 60%,#dfe3e6)}
.card{top:625px;width:275px;height:166px;background:#fff;box-shadow:0 0 6px rgba(0,0,0,.25);padding:8px 14px}
.card h2{font-size:22px;font-weight:300;color:var(--green-dark)}
.card p{font-size:12.5px;line-height:18.5px;margin-top:2px;color:#333}
.more{position:absolute;left:-7px;top:102px;height:22px;line-height:22px;padding:0 18px 0 15px;font-size:12px;color:#222;background:var(--green);clip-path:polygon(0 0,90% 0,100% 50%,90% 100%,0 100%)}
.more::after{content:"";position:absolute;left:0;top:22px;border-left:7px solid transparent;border-top:6px solid var(--green-dark)}
.news{left:774px;top:454px;width:263px;height:337px;background:var(--panel);padding:6px}
.news-in{background:#fff;height:100%;padding:0 12px}
.tabs{display:flex;gap:2px;margin-left:-6px;padding-top:6px}
.tabs div{height:30px;line-height:30px;font-size:13px;padding:0 10px;display:flex;align-items:center;gap:6px}
.tabs .t-on{color:#1f5a99;width:88px;padding-left:22px}
.tabs .t-off{background:linear-gradient(#f4f4f4,#dcdcdc);color:#333;width:80px;justify-content:center}
.ico{width:14px;height:14px;border-radius:3px}
.item{border-bottom:1px dotted #999;padding:7px 0 6px}
.item:last-child{border:0}
.item p{font-size:12px;line-height:16.5px;color:#777}
.item time{display:block;font-size:11px;color:#444;margin-top:4px}
.signup h2{font-size:22px;font-weight:300;color:var(--green-dark)}
.signup{left:164px;top:803px}
.field{top:835px;width:216px;height:29px;border:1px solid #ccc;font-size:11.5px;line-height:27px;padding-left:6px;color:#333}
.btn{left:620px;top:835px;width:92px;height:29px;background:linear-gradient(var(--green-light),var(--green));font-size:14px;line-height:29px;text-align:center;color:#222}
.call{left:819px;top:824px;display:flex;gap:14px;align-items:center}
.call .icon{width:40px;height:40px;background:var(--green);display:flex;align-items:center;justify-content:center}
.call small{display:block;font-size:13px;color:#555}
.call strong{display:block;font-size:21px;font-weight:400;color:#111;line-height:22px}
.footer{left:164px;top:893px;width:871px;height:231px;border:1px solid var(--line)}
.col{position:absolute;top:20px}
.col h3{font-size:14px;font-weight:600;color:#555;margin-bottom:8px}
.col li{list-style:none;font-size:11.5px;line-height:27.7px;color:#666}
.follow{position:absolute;right:22px;top:18px;text-align:right;font-size:13px;color:#555}
.social{display:flex;gap:6px;justify-content:flex-end;margin-top:10px}
.social span{width:18px;height:18px;border-radius:2px}
.legal{font-size:11.5px;color:#555;margin-top:19px}
</style>
</head>
<body>
<div class="abs logo"><span>BrightForge</span><span class="mark"></span></div>
<nav class="abs nav">
  <a class="active" href="#">Home</a><a href="#">About us</a><a href="#">Services</a><a href="#">Testimonials</a><a href="#">Blog</a><a href="#">Contact</a>
</nav>

<div class="abs hero" role="img" aria-label="Photo of a smiling business team in a meeting around a table"></div>
<div class="abs dots"><span></span><span class="on"></span><span></span><span></span><span></span><span></span></div>

<section class="abs welcome">
  <h1>Welcome to BrightForge</h1>
  <p>Lorem Ipsum is simply dummy text of the printing and typesetting industry. Lorem Ipsum has been the industry's standard dummy text ever since the 1500s, when an unknown printer took a galley of type and scrambled it to make a type specimen book. It has survived not only five centuries, but also.</p>
</section>
<div class="abs thumb" role="img" aria-label="Photo of a businessman on the phone by an office window"></div>

<article class="abs card" style="left:164px">
  <h2>Services</h2>
  <p>Business Strategy, Creative Consultancy, Communications and Strategic Planning, Professional Development, Change Management..</p>
  <span class="more">Read More &gt;&gt;</span>
</article>
<article class="abs card" style="left:469px">
  <h2>Testimonials</h2>
  <p>Business Strategy, Creative Consultancy, Communications and Strategic Planning, Professional Development, Change Management..</p>
  <span class="more">Read More &gt;&gt;</span>
</article>

<aside class="abs news">
  <div class="news-in">
    <div class="tabs">
      <div class="t-on">News</div>
      <div class="t-off">Blog <span class="ico" style="background:#f07a1a"></span></div>
      <div class="t-off">Tweets <span class="ico" style="background:#4fb0e0"></span></div>
    </div>
    <div class="item" style="padding-top:14px"><p>Webinar: Effective Application Security Risk Management - From Standards to Best Prac-tices</p><time>Oct 23, 2012</time></div>
    <div class="item"><p>Lumen Guard Announces CrewCoach Version 3.2</p><time>Oct 23, 2012</time></div>
    <div class="item"><p>Webinar: Effective Application Security Risk Management - From Policy to Standards</p><time>Oct 23, 2012</time></div>
    <div class="item"><p>Webinar: Addressing Application Security Requirements of the PCI-DSS</p><time>Oct 23, 2012</time></div>
  </div>
</aside>

<div class="abs signup"><h2>Newsletter signup</h2></div>
<div class="abs field" style="left:164px">Enter the Name</div>
<div class="abs field" style="left:390px">Enter the E mail id</div>
<div class="abs btn">Sign Up</div>

<div class="abs call">
  <div class="icon"><svg width="24" height="24" viewBox="0 0 24 24"><path fill="#fff" d="M6.6 2.5c.6-.3 1.2 0 1.5.5l2 3.6c.3.6.2 1.2-.3 1.6L8.3 9.4c1.1 2.5 3.1 4.7 5.6 5.9l1.3-1.5c.4-.5 1.1-.6 1.6-.3l3.6 2c.5.3.8 1 .5 1.5l-1 2.4c-.3.7-1 1.1-1.8 1C9.8 19.8 4.2 14.2 3.6 6c-.1-.8.3-1.5 1-1.8z"/></svg></div>
  <div><small>Call Us Now on</small><strong>555.XXX.XXXX</strong></div>
</div>

<footer class="abs footer">
  <div class="col" style="left:41px">
    <h3>COMPANY</h3>
    <ul><li>Company</li><li>Clients</li><li>News &amp; Events</li><li>Partners</li><li>Contact Us</li></ul>
  </div>
  <div class="col" style="left:192px">
    <h3>SERVICES</h3>
    <ul><li>Business Strategy</li><li>Communications and Strategic Planning</li><li>Creative Consultancy</li><li>Professional Development</li><li>Change Management</li><li>Project Management</li></ul>
  </div>
  <div class="follow">
    Follow Us on
    <div class="social"><span style="background:#3b5998"></span><span style="background:#4fb0e0"></span><span style="background:#1f6fa8"></span><span style="background:#f07a1a"></span></div>
    <div class="legal">Terms &amp; Conditions &nbsp;|&nbsp; Privacy Policy</div>
  </div>
</footer>
</body>
</html>
```